Veldmark Supplies Business Card

Professional business card that stand out to our potential customers. Front and back with clean modern design

Industry/Entity Type

Oil and gas

Contact Information for Business Card

Name, address, website , office phone and cell number

Requirements
Must have
• Editable files for each employee

```html
<!DOCTYPE html>
<html lang="en">
<head>
<meta charset="utf-8">
<title>Veldmark Supplies Business Card</title>
<link href="https://fonts.googleapis.com/css2?family=Roboto:wght@400;500;700;900&display=swap" rel="stylesheet">
<style>
  :root {
    --brand-red: #e11d24;
    --brand-blue: #21a9d1;
    --card-white: #fbfbfb;
    --backdrop: #d9d9db;
    --ink-white: #ffffff;
  }
  * { margin: 0; padding: 0; box-sizing: border-box; }
  html, body { width: 1200px; height: 852px; overflow: hidden; }
  body {
    background: var(--backdrop);
    font-family: "Roboto", Arial, sans-serif;
    position: relative;
  }
  .card {
    position: absolute;
    top: 283px;
    width: 500px;
    height: 286px;
    border-radius: 18px;
    overflow: hidden;
    background: var(--card-white);
    box-shadow: 0 10px 28px rgba(0,0,0,0.18);
  }
  .card--back { left: 70px; }
  .card--front { left: 630px; }

  /* Back side */
  .back-brand {
    position: absolute;
    left: 0; right: 0; top: 118px;
    display: flex; align-items: center; justify-content: center; gap: 12px;
  }
  .brand-square {
    width: 22px; height: 22px;
    background: var(--brand-blue);
  }
  .brand-name {
    font-weight: 900;
    text-transform: uppercase;
    color: var(--brand-red);
    letter-spacing: 0.5px;
  }
  .back-brand .brand-name { font-size: 28px; }
  .edge-strip {
    position: absolute; left: 0; right: 0; bottom: 0; height: 7px;
    display: flex;
  }
  .edge-strip .red { flex: 1; background: var(--brand-red); }
  .edge-strip .blue { flex: 1; background: var(--brand-blue); }

  /* Front side */
  .front-bands { position: absolute; inset: 0; }
  .front-brand {
    position: absolute; left: 24px; top: 72px;
    font-size: 22px;
  }
  .person {
    position: absolute; left: 24px; top: 120px;
    color: var(--ink-white);
  }
  .person-name { font-size: 17px; font-weight: 700; }
  .person-title { font-size: 10px; font-weight: 400; margin-top: 2px; }
  .contact-list {
    position: absolute; left: 24px; top: 186px;
    list-style: none;
    color: var(--ink-white);
    font-size: 10.5px;
    line-height: 16px;
  }
  .contact-list li { display: flex; align-items: center; gap: 7px; }
  .contact-list svg { width: 10px; height: 10px; fill: var(--ink-white); }
  .contact-list .address { margin-top: 2px; }
</style>
</head>
<body>

<section class="card card--back" aria-label="Card back">
  <div class="back-brand">
    <span class="brand-square"></span>
    <span class="brand-name">Veldmark Supplies</span>
  </div>
  <div class="edge-strip"><span class="red"></span><span class="blue"></span></div>
</section>

<section class="card card--front" aria-label="Card front">
  <svg class="front-bands" viewBox="0 0 500 286" preserveAspectRatio="none" aria-hidden="true">
    <rect x="0" y="105" width="310" height="70" fill="var(--brand-blue)"/>
    <polygon points="0,175 310,175 310,60 500,60 500,286 0,286" fill="var(--brand-red)"/>
    <rect x="440" y="0" width="60" height="60" fill="var(--brand-blue)"/>
    <rect x="345" y="30" width="125" height="125" fill="var(--card-white)"/>
  </svg>

  <div class="brand-name front-brand">Veldmark Supplies</div>

  <div class="person">
    <div class="person-name">Jordan Hale</div>
    <div class="person-title">Managing Director</div>
  </div>

  <ul class="contact-list">
    <li>
      <svg viewBox="0 0 10 10"><path d="M2 0.5 L4 0.5 L4.6 2.8 L3.4 3.6 Q4.2 5.6 6.3 6.6 L7.1 5.4 L9.5 6 L9.5 8 Q9.5 9.5 8 9.5 Q1 9 0.5 2 Q0.5 0.5 2 0.5Z"/></svg>
      (555)014-0237
    </li>
    <li>
      <svg viewBox="0 0 10 10"><path d="M0.5 2 L9.5 2 L9.5 8.5 L0.5 8.5Z M1.2 2.6 L5 5.6 L8.8 2.6" stroke="#e11d24" stroke-width="0.8"/></svg>
      sales@veldmarksupplies.com
    </li>
    <li>
      <svg viewBox="0 0 10 10"><circle cx="5" cy="5" r="4.5"/><path d="M0.5 5 H9.5 M5 0.5 V9.5" stroke="#e11d24" stroke-width="0.7"/></svg>
      www.veldmarksupplies.com
    </li>
    <li class="address">410 Larkfield Ave Suite 3 Midland, Tx 79701</li>
  </ul>
</section>

</body>
</html>
```